Web site for new fundraising service for charities

We need a web design for a new charitable trust based in New Zealand. With the economic downturn, charities are finding it increasingly difficult to raise the monies they need to deliver their services.

Using a network of fundraisers working out of their homes, KindLoop (our charitable trust) will source unique, high interest auction items on behalf of multiple charities - things like luxury cruises, exotic travel, luxury accommodation, fine dining, unique experiences with sports and entertainment personalities, tickets to sporting and entertainment events, etc.

Once we have sourced sufficient high value items we will then partner with BidNest (NZ's equivalent of uLot) to launch the auction. The proceeds from each auction will benefit up to 6 charities. The auctions will be promoted through BidNest, through PR, and through the communications channels of the benefiting charities, reaching a wider audience than would be possible if just one charity was holding an auction and therefore resulting in more competitive bidding and higher returns for the charities.

We need a web site that we can point potential donors of auction items to, that gives them confidence in KindLoop. We will also leverage the web site with journalists. And of course, charities who are wondering whether or not to use KindLoop will come to our web site and check out our credentials. The tone of the site needs to be warm, friendly, approachable.

We are not locked into the blue and orange colors of the logo and in fact are experimenting with other colors as we speak.

Please note that what we're looking for is the design for the home page, plus a sub page design.

CEOs, corporate social responsibility managers, general managers, business owners, charities, the media

Communications

• Video on home page
Newsletter sign up on all pages
Navigation as per the attached PDF example

```html
<!DOCTYPE html>
<html lang="en">
<head>
<meta charset="utf-8">
<title>KindLoop – Charity Auctions</title>
<link rel="stylesheet" href="https://fonts.googleapis.com/css2?family=Lato:ital,wght@0,300;0,400;0,700;1,700&display=swap">
<style>
:root{
  --bg:#f1f1f1;
  --bg-deep:#e2e2e2;
  --ink:#3f3f3f;
  --muted:#666;
  --navy:#1f3f8f;
  --navy-dark:#16223f;
  --orange:#e0961f;
  --orange-dark:#c57d10;
  --blue-btn:#0c7fb8;
  --blue-btn-dark:#075a8c;
  --rule:#c9c9c9;
  --frame:#5c5f63;
  --quote-mark:#d6d6d6;
  --white:#fff;
}
*{box-sizing:border-box;margin:0;padding:0}
html,body{width:1200px;height:707px;overflow:hidden}
body{font-family:"Lato",sans-serif;color:var(--ink);background:var(--bg);position:relative}
.backdrop{position:absolute;inset:0;background:radial-gradient(ellipse at 50% 45%,#f7f7f7 0%,var(--bg) 55%,var(--bg-deep) 100%)}
.abs{position:absolute}

/* header */
.brand{left:203px;top:38px;display:flex;align-items:center;gap:10px;font-size:30px;font-weight:700;color:var(--navy);letter-spacing:-.5px}
.brand-dot{width:48px;height:48px;border-radius:50%;background:var(--orange)}
.main-nav{left:473px;top:54px;display:flex;font-size:17px;font-weight:400;color:#333}
.main-nav a{padding:0 12px;border-left:1px dotted #aaa;color:inherit;text-decoration:none;line-height:20px}
.main-nav a:first-child{border-left:none}
.social{display:flex;gap:16px;font-size:11px;font-weight:700;color:#555}
.social-top{left:858px;top:57px}
.header-rule{left:188px;top:96px;width:810px;height:1px;background:var(--rule)}

/* side menu */
.side-menu{left:212px;top:148px;width:180px;height:217px;background:linear-gradient(#f9f9f9,#dde2e6);border:1px solid #ccc;border-radius:3px;box-shadow:0 8px 10px -6px rgba(0,0,0,.35)}
.side-menu ul{list-style:none;padding-top:4px}
.side-menu li{height:35.5px;line-height:35px;text-align:right;padding-right:24px;font-size:13px;margin:0 0 0 22px;border-bottom:1px dotted #bbb}
.side-menu li:last-child{border-bottom:none}
.side-menu li.active{margin-left:-6px;background:linear-gradient(90deg,var(--navy-dark),#1b3475);color:var(--white);height:27px;line-height:27px;clip-path:polygon(0 0,100% 0,100% 100%,0 100%,6px 50%)}

/* video */
.video{left:385px;top:122px;width:415px;height:260px;background:var(--frame);border:1px solid #444;padding:7px}
.video-still{width:100%;height:100%;background:linear-gradient(#555 0%,#3c3c3c 55%,#2b2b2b 100%);border:1px solid #333}
.play{left:156px;top:74px;width:92px;height:92px;border-radius:50%;background:radial-gradient(circle at 45% 35%,#fff,#bdbdbd);border:5px solid #8b8b8b;box-shadow:0 3px 8px rgba(0,0,0,.5)}

/* subscribe */
.subscribe{left:800px;top:148px;width:193px;height:218px;background:linear-gradient(var(--orange),var(--orange-dark));border-radius:0 3px 3px 0;padding:8px 10px;color:var(--white)}
.subscribe h2{font-size:23px;font-weight:400;margin-bottom:4px}
.subscribe p{font-size:9.4px;line-height:12.4px;margin-bottom:9px}
.field{background:var(--white);height:19px;font-size:9.5px;color:#aaa;padding:3px 6px;margin-bottom:5px}
.row{display:flex;gap:5px}.row .field{flex:1}
.submit{height:25px;background:linear-gradient(#1c98cf,var(--blue-btn-dark));border:1px solid #064a72;text-align:center;font-size:18px;font-weight:700;line-height:23px}

/* quote */
.quote-mark{font-size:130px;color:var(--quote-mark);font-weight:700;line-height:1;z-index:0}
.quote-open{left:212px;top:386px}
.quote-close{left:836px;top:492px;font-size:80px}
.quote{left:268px;top:424px;font-size:20.5px;line-height:25px;color:var(--muted);font-weight:400;z-index:1}
.quote span{display:block;white-space:nowrap}
.cite{left:268px;top:537px;font-size:21px;font-weight:700;font-style:italic;color:var(--orange-dark);z-index:1}

/* footer */
.footer-rule{left:196px;width:810px;height:1px;background:var(--rule)}
.foot-dot{left:203px;top:616px;width:26px;height:26px;border-radius:50%;background:#9a9a9a}
.foot-nav{left:346px;top:621px;display:flex;gap:15px;font-size:10.5px;color:#555}
.social-foot{left:850px;top:622px}
.copy{left:0;width:1200px;top:666px;text-align:center;font-size:10px;color:#555}
</style>
</head>
<body>
<div class="backdrop" role="img" aria-label="Faded collage of holiday photographs behind the page"></div>

<header>
  <div class="abs brand"><span class="brand-dot"></span>KindLoop</div>
  <nav class="abs main-nav"><a href="#">DONOR</a><a href="#">CHARITIES</a><a href="#">AUCTIONS</a></nav>
  <div class="abs social social-top"><span>Friendly</span><span>Chirp</span><span>Connectly</span><span>Feed</span></div>
  <div class="abs header-rule"></div>
</header>

<nav class="abs side-menu">
  <ul>
    <li class="active">Home</li>
    <li>How it Works</li>
    <li>Acts of Goodness</li>
    <li>Goodness Partners</li>
    <li>About</li>
    <li>Contact</li>
  </ul>
</nav>

<section class="abs video">
  <div class="video-still" role="img" aria-label="Video still of an overwater bungalow at dusk"></div>
  <div class="abs play">
    <svg width="82" height="82" viewBox="0 0 82 82"><polygon points="33,26 33,52 56,39" fill="#111"/></svg>
  </div>
</section>

<aside class="abs subscribe">
  <h2>Subscribe</h2>
  <p>Charity auctions are a great way to get luxury items and unique experiences while helping a worthwhile cause. Subscribe to our email list to be kept informed about upcoming auctions.</p>
  <div class="row"><div class="field">First Name</div><div class="field">Last Name</div></div>
  <div class="field">City / Town</div>
  <div class="field">Email Address</div>
  <div class="submit">Submit</div>
</aside>

<section>
  <div class="abs quote-mark quote-open">“</div>
  <div class="abs quote-mark quote-close">”</div>
  <blockquote class="abs quote">
    <span>In the end, though, maybe we must all give up trying to pay back the people</span>
    <span>in this world who sustain our lives. In the end, maybe it’s wiser to surrender</span>
    <span>before the miraculous scope of human generosity and to just keep saying</span>
    <span>thank you, forever and sincerely, for as long as we have voices.</span>
  </blockquote>
  <div class="abs cite">— Eleanor Grant</div>
</section>

<footer>
  <div class="abs footer-rule" style="top:597px"></div>
  <div class="abs foot-dot"></div>
  <nav class="abs foot-nav"><span>Home</span><span>How it Works</span><span>Acts of Goodness</span><span>Goodness Partners</span><span>About</span><span>Contact</span></nav>
  <div class="abs social social-foot"><span>Friendly</span><span>Chirp</span><span>Connectly</span><span>Feed</span></div>
  <div class="abs footer-rule" style="top:655px"></div>
  <p class="abs copy">Copyrights © KindLoop. All rights reserved.</p>
</footer>
</body>
</html>
```